Clinic for cellulit and fat removal

Name of clinic :
Lirava
- Body & Health (this has to be written on the site.)
I need CMS for me to be able to make changes myself.
A webpage for woman searching for a solution to remove fat and cellulit.
The owner is a brazilian woman in Denmark, and want her sense of aestetic shines thru the website.
There needs to be a slide show on the landing page showing big sliding pictures, of the clinic and and the treatments.
The Cryolipolysis, is a treatment freezing fat and cellulit, and this treatment will be the Attraction of the clinic.
Needs These pages in a horisontal fasion. (written in Danish)
Lirava
Behandlinger
- Cryolipolysis
- Trimflox
- Lymfemassage
- Korathelix
- Amberline Tide
Produkter
Priser
Kontakt
Clinic
Coded - Design and coding required
5+ page

```html
<!DOCTYPE html>
<html lang="da">
<head>
<meta charset="utf-8">
<title>Lirava – Kontakt</title>
<link href="https://fonts.googleapis.com/css2?family=Open+Sans:wght@400;600&family=Damion&display=swap" rel="stylesheet">
<style>
  :root {
    --mint: #8ed1b7;
    --mint-soft: #e3f7ef;
    --mint-line: #bfe6d6;
    --pink: #b5317f;
    --ink: #1f1f1f;
    --muted: #7aa99a;
    --paper: #ffffff;
    --map-light: #f1f2f1;
  }
  * { box-sizing: border-box; margin: 0; padding: 0; }
  html, body { width: 1200px; height: 675px; overflow: hidden; background: var(--paper); }
  body { font-family: "Open Sans", Arial, sans-serif; color: var(--ink); position: relative; }

  .sidebar { position: absolute; left: 0; top: 0; width: 200px; height: 675px; background: var(--paper); box-shadow: 2px 0 8px rgba(0,0,0,.05); z-index: 2; }
  .brand { position: absolute; left: 34px; top: 34px; display: flex; align-items: center; gap: 8px; }
  .brand-dot { width: 12px; height: 12px; border-radius: 50%; background: var(--mint); }
  .brand-name { font-size: 30px; font-weight: 400; color: var(--ink); letter-spacing: .5px; line-height: 1; }
  .brand-tagline { position: absolute; left: 55px; top: 76px; font-size: 11px; font-weight: 400; color: var(--ink); letter-spacing: .4px; }

  .main-nav { position: absolute; left: 0; top: 137px; width: 200px; list-style: none; }
  .main-nav li { height: 46.6px; border-top: 1px dashed var(--mint-line); display: flex; align-items: center; padding-left: 30px; font-size: 11px; letter-spacing: .3px; }
  .main-nav li:last-child { border-bottom: 1px dashed var(--mint-line); }
  .main-nav li.is-active { background: var(--mint-soft); box-shadow: inset -2px 0 0 var(--mint); border-top-color: transparent; }

  .social-links { position: absolute; left: 34px; top: 616px; display: flex; gap: 6px; align-items: center; list-style: none; }
  .social-links li { width: 28px; height: 28px; display: flex; align-items: center; justify-content: center; }
  .social-links li span { width: 8px; height: 8px; border-radius: 50%; background: var(--mint); }
  .social-links li.is-featured { border-radius: 50%; background: var(--mint); }
  .social-links li.is-featured span { background: var(--paper); }

  .map-area { position: absolute; left: 200px; top: 0; width: 490px; height: 675px;
    background: linear-gradient(120deg, var(--map-light) 0%, var(--map-light) 55%, #cfeadf 75%, var(--mint) 100%); }

  .contact { position: absolute; left: 690px; top: 0; width: 510px; height: 675px; }
  .contact-title { position: absolute; left: 0; width: 510px; top: 24px; text-align: center; font-family: "Damion", cursive; font-size: 50px; color: var(--pink); font-weight: 400; }
  .contact-details { position: absolute; left: 108px; top: 130px; width: 300px; list-style: none; }
  .contact-details li { display: flex; align-items: flex-start; font-size: 10.5px; line-height: 1.3; }
  .contact-details li + li { margin-top: 17px; }
  .contact-details svg { width: 10px; height: 10px; margin: 2px 16px 0 0; flex: none; fill: var(--mint); }
  .contact-intro { position: absolute; left: 0; width: 510px; top: 254px; text-align: center; color: var(--pink); font-size: 10.5px; line-height: 1.2; }

  .contact-form { position: absolute; left: 100px; top: 297px; width: 306px; }
  .field { display: block; width: 100%; height: 31px; border: 1px solid var(--mint); border-radius: 2px; padding: 0 9px; font-family: inherit; font-size: 10.5px; color: var(--muted); line-height: 29px; margin-bottom: 10px; background: var(--paper); }
  .field.message { height: 125px; line-height: 1; padding-top: 10px; margin-bottom: 10px; }
  .submit { display: block; margin-left: auto; width: 75px; height: 31px; border: 0; border-radius: 2px; background: var(--pink); color: var(--paper); font-family: inherit; font-size: 11px; font-weight: 600; }

  .copyright { position: absolute; right: 22px; top: 632px; font-size: 9px; color: var(--ink); }
</style>
</head>
<body>
  <aside class="sidebar">
    <div class="brand"><span class="brand-dot"></span><span class="brand-name">Lirava</span></div>
    <div class="brand-tagline">Body &amp; Health</div>
    <ul class="main-nav">
      <li>Lirava</li>
      <li>Behandlinger</li>
      <li>Produkter</li>
      <li>Priser</li>
      <li class="is-active">Kontakt</li>
    </ul>
    <ul class="social-links" aria-label="Sociale medier">
      <li class="is-featured"><span></span></li>
      <li><span></span></li>
      <li><span></span></li>
      <li><span></span></li>
    </ul>
  </aside>

  <div class="map-area" role="img" aria-label="Kort over København med klinikkens beliggenhed, lysegrå gader og mintgrønt vand"></div>

  <section class="contact">
    <h1 class="contact-title">Kontakt</h1>
    <ul class="contact-details">
      <li><svg viewBox="0 0 10 10"><path d="M5 0a3.5 3.5 0 0 0-3.5 3.5C1.5 6 5 10 5 10s3.5-4 3.5-6.5A3.5 3.5 0 0 0 5 0zm0 5a1.4 1.4 0 1 1 0-2.8A1.4 1.4 0 0 1 5 5z"/></svg>Solvænget 14, Rørvig, Region Sjælland,<br>Denmark 4581</li>
      <li><svg viewBox="0 0 10 10"><path d="M2 .5l1.6 2-1 1.2a6 6 0 0 0 3.7 3.7l1.2-1 2 1.6-.9 1.5C4.8 9.5.5 5.2.5 1.4z"/></svg>(+45) 42-18-63-07</li>
      <li><svg viewBox="0 0 10 10"><circle cx="5" cy="5" r="5"/><path d="M2.5 3.5h5v3.2h-5z M2.5 3.5L5 5.4 7.5 3.5" fill="none" stroke="#fff" stroke-width=".7"/></svg>info@liravabodyandhealth.com</li>
    </ul>
    <p class="contact-intro">For yderligere information, send os en besked ved<br>at udfylde op nedenstående formular</p>
    <form class="contact-form">
      <div class="field">Name</div>
      <div class="field">Email</div>
      <div class="field">Subject</div>
      <div class="field message">Message</div>
      <button class="submit" type="button">Submit</button>
    </form>
    <p class="copyright">© Copyright Lirava 2017</p>
  </section>
</body>
</html>
```